Business card for law firm

Need business card for new law firm. Think confident, authoritative, conservative, but not stuffy or old-fashioned.

Contact Information for Business Card

Content for card - logo (uploaded), plus the following:

Paul Whitcombe (larger font)
Managing Partner (larger font, but not as large as name)
Level 9, 7 Ferris Lane
Sydney NSW 2000
Main Tel 02 9364 2710
Direct Tel 02 8472 3159
Email paul@qvlegal.com.au
www.qvlegal.com.au

Letterhead design should include logo plus:
Level 9, 7 Ferris Lane
Sydney NSW 2000
Tel 02 8472 3159
www.qvlegal.com.au

```html
<!DOCTYPE html>
<html lang="en">
<head>
<meta charset="utf-8">
<title>Quayvale Legal – Business Card</title>
<link rel="stylesheet" href="https://fonts.googleapis.com/css2?family=Roboto:wght@400;500;700&display=swap">
<style>
  :root {
    --navy: #001a52;
    --ink: #1a1a1a;
    --grey-text: #585858;
    --paper: #ffffff;
    --backdrop: #e4e4e4;
  }
  * { margin: 0; padding: 0; box-sizing: border-box; }
  html, body {
    width: 1146px;
    height: 1200px;
    overflow: hidden;
    background: var(--backdrop);
    font-family: "Roboto", Arial, sans-serif;
  }
  .canvas { position: relative; width: 1146px; height: 1200px; }

  .card {
    position: absolute;
    left: 207px;
    width: 729px;
    height: 422px;
  }
  .card--front { top: 124px; background: var(--paper); }
  .card--back { top: 654px; background: var(--navy); }

  /* Firm name block */
  .brand {
    position: absolute;
    left: 250px;
    top: 46px;
    width: 240px;
    transform: translateX(-50%);
    left: 162px;
    text-align: center;
    color: var(--ink);
  }
  .brand__square {
    display: block;
    width: 44px;
    height: 44px;
    margin: 0 auto 20px;
    background: var(--navy);
  }
  .brand__name {
    font-size: 36px;
    font-weight: 400;
    letter-spacing: 1px;
    line-height: 1;
  }
  .brand__sub {
    margin-top: 8px;
    font-size: 13px;
    font-weight: 400;
    letter-spacing: 9px;
    padding-left: 9px;
    line-height: 1;
  }

  /* Contact details */
  .contact {
    position: absolute;
    left: 44px;
    top: 238px;
    color: var(--grey-text);
    font-size: 17px;
    line-height: 21px;
  }
  .contact__group + .contact__group { margin-top: 10px; }
  .contact__web { font-weight: 500; font-size: 18px; }

  /* Person */
  .person {
    position: absolute;
    right: 46px;
    top: 278px;
    text-align: right;
  }
  .person__name {
    color: var(--navy);
    font-size: 35px;
    font-weight: 700;
    line-height: 38px;
    letter-spacing: -0.3px;
  }
  .person__title {
    color: var(--ink);
    font-size: 22px;
    font-weight: 500;
    line-height: 24px;
  }
  .accent-bar {
    position: absolute;
    right: 0;
    top: 278px;
    width: 16px;
    height: 59px;
    background: var(--navy);
  }

  /* Back */
  .back-mark {
    position: absolute;
    right: 45px;
    bottom: 38px;
    text-align: right;
    color: var(--paper);
  }
  .back-mark__square {
    display: inline-block;
    width: 40px;
    height: 40px;
    background: var(--paper);
    margin-bottom: 12px;
  }
  .back-mark__name {
    font-size: 20px;
    font-weight: 400;
    letter-spacing: 2px;
  }
</style>
</head>
<body>
<main class="canvas">
  <section class="card card--front">
    <div class="brand">
      <span class="brand__square"></span>
      <div class="brand__name">QUAYVALE</div>
      <div class="brand__sub">LEGAL</div>
    </div>

    <address class="contact" style="font-style:normal">
      <div class="contact__group">
        <div>Level 9, 7 Ferris Lane</div>
        <div>Sydney NSW 2000</div>
      </div>
      <div class="contact__group">
        <div>02 9364 2710 (Main)</div>
        <div>02 8472 3159 (Direct)</div>
        <div>paul@qvlegal.com.au</div>
      </div>
      <div class="contact__group contact__web">www.qvlegal.com.au</div>
    </address>

    <div class="person">
      <div class="person__name">Paul Whitcombe</div>
      <div class="person__title">Managing Partner</div>
    </div>
    <span class="accent-bar"></span>
  </section>

  <section class="card card--back">
    <div class="back-mark">
      <span class="back-mark__square"></span>
      <div class="back-mark__name">QUAYVALE</div>
    </div>
  </section>
</main>
</body>
</html>
```